PostCard Design Project

I am making a mailing postcard
I am having the mailing printed using 4 color foil on certain parts.
I am looking for a design that maximizes the foil process where certain parts are done in foil to grab the customers attention (example: if there is a car on the postcard the headlights would be done in foil) .
I am targeting some industries, (auto, real estate, medical, beauty) I would like the post card to have examples of postcard ideas for 2 or 3 of these industries.
specs:
the postcard should be atleast 6.5x9 up to 8.5x11, I don't want to restrict the space for the creative as I don't want everything to look like a huge mess. both sides will be used.
the piece is a direct mail piece so it has to meet requirements of https://www.mailvantor.com/business/pdf/quick-reference-guide.pdf
text will be
"business with no limits, meet mailing with no addresses, gain new customers through "Open Porch Route Drop" reach new customers at their home without needing their address. "
I also want some current print specials I am running included.
-double your order FREE (order 500 business cards and get 1000)
-250 100lb gloss stock brochures 99.00
-business packages (cards, envelopes and letterhead) 299
-1000 flyers 140.40
-5000 postcards 179.99
A list of services
banners
booklets
brochures
business cards
calendars
catalogs
CD/DVD packages
envelopes
event tickets
flyers
hangtags
postcards
posters
presentation folders
rack cards
labels
table tents
window cling and decal
"order 24/7 orders@inkwillow.com" must be included
my logo is InkWillow will be supplied later
ive received some great designs. however Im looking for something a little more modern like some zorvel would put out. if the amount of words is too much please feel free to edit. also an idea i had for the list of services i offer is to have it transparent yet readable as the background of the postcard some small some big but covering the entire backgroud. you can then design on top of that with other thing. just an early morning thought
Reason: I have uploaded a sketch of my idea, please take time to look at it for an accurate depiction of what im looking for. feel free to add elements that make it pop off the page
Reason: We are getting close i will be providing feed back today

```html
<!DOCTYPE html>
<html lang="en">
<head>
<meta charset="utf-8">
<title>InkWillow Postcard – Front and Back</title>
<link rel="stylesheet" href="https://fonts.googleapis.com/css2?family=Montserrat:wght@800&family=Open+Sans:wght@400;600;700&display=swap">
<style>
  :root {
    --stage: #e9e6e1;
    --card: #0b0b0b;
    --lime: #b6d335;
    --cyan: #2aa8d8;
    --grey: #5b5b5b;
    --white: #ffffff;
    --paper-shadow: rgba(0,0,0,0.35);
  }
  * { box-sizing: border-box; margin: 0; padding: 0; }
  html, body { width: 1200px; height: 900px; overflow: hidden; }
  body {
    background: var(--stage);
    font-family: "Open Sans", Arial, sans-serif;
    position: relative;
  }
  .postcard {
    position: absolute;
    top: 256px;
    width: 580px;
    height: 387px;
    background: var(--card);
    overflow: hidden;
    box-shadow: 0 10px 24px var(--paper-shadow);
  }
  .postcard--front { left: 15px; }
  .postcard--back { left: 605px; }

  /* Front */
  .bokeh { position: absolute; inset: 0; }
  .headline {
    position: absolute;
    left: 22px; top: 30px;
    width: 360px;
    font-family: "Montserrat", Arial, sans-serif;
    font-weight: 800;
    font-size: 19px;
    line-height: 1.2;
    color: var(--lime);
    letter-spacing: 0.3px;
    white-space: nowrap;
  }
  .sample-collage {
    position: absolute;
    left: 22px; top: 96px;
    width: 350px; height: 178px;
    background: linear-gradient(120deg, #c9372c 0%, #e9e2d0 35%, #f1c6a8 55%, #c5d98a 75%, #4b8fc0 100%);
  }
  .model-photo {
    position: absolute;
    right: 16px; top: 14px;
    width: 170px; height: 118px;
    background: linear-gradient(160deg, #d9e6ee 0%, #c89a7e 50%, #3c87c4 100%);
  }
  .offer-banner {
    position: absolute;
    right: 16px; top: 146px;
    width: 170px; height: 34px;
    background: var(--lime);
    color: var(--card);
    font-weight: 700;
    font-size: 15px;
    line-height: 34px;
    text-align: center;
  }
  .offer-list {
    position: absolute;
    right: 16px; top: 190px;
    width: 170px;
    list-style: none;
    color: var(--lime);
    font-size: 10px;
    line-height: 1.35;
  }
  .offer-list li::before { content: "• "; }
  .route-drop {
    position: absolute;
    left: 22px; top: 290px;
    width: 165px;
    color: var(--white);
    font-size: 10px;
    line-height: 1.4;
  }
  .route-drop strong { color: var(--lime); font-weight: 700; }
  .order-info {
    position: absolute;
    left: 200px; top: 290px;
    color: var(--lime);
    font-weight: 600;
    font-size: 17px;
    line-height: 1.25;
  }
  .logo-placeholder {
    color: var(--white);
    font-weight: 400;
    font-size: 15px;
    margin-top: 6px;
  }

  /* Back */
  .service-field {
    position: absolute;
    inset: 0;
    padding: 4px 0 0 0;
    font-weight: 600;
    font-size: 17px;
    line-height: 25px;
    white-space: nowrap;
    color: var(--grey);
  }
  .service-row { display: block; }
  .service--cyan { color: var(--cyan); }
  .service--lime { color: var(--lime); }
  .stamp-zone {
    position: absolute;
    right: 14px; top: 0;
    width: 110px; height: 80px;
    background: var(--card);
    display: flex;
    align-items: center;
    justify-content: center;
  }
  .stamp-box {
    width: 72px; height: 48px;
    background: var(--white);
    color: var(--card);
    font-size: 9px;
    line-height: 1.2;
    text-align: center;
    display: flex;
    align-items: center;
    justify-content: center;
  }
</style>
</head>
<body>

<section class="postcard postcard--front" aria-label="Postcard front">
  <svg class="bokeh" width="580" height="387" aria-hidden="true">
    <circle cx="40" cy="30" r="28" fill="#6b5a3c" opacity="0.55"/>
    <circle cx="110" cy="60" r="22" fill="#8a9a3a" opacity="0.45"/>
    <circle cx="200" cy="24" r="30" fill="#4d5a2a" opacity="0.5"/>
    <circle cx="300" cy="70" r="24" fill="#777" opacity="0.35"/>
    <circle cx="360" cy="20" r="26" fill="#8a9a3a" opacity="0.5"/>
    <circle cx="30" cy="110" r="32" fill="#6b5a3c" opacity="0.45"/>
    <circle cx="250" cy="110" r="20" fill="#8a9a3a" opacity="0.35"/>
    <circle cx="60" cy="340" r="30" fill="#4d4d4d" opacity="0.45"/>
  </svg>

  <h1 class="headline">LET US MAKE YOUR BUISSNESS<br>SHINE !</h1>

  <div class="sample-collage" role="img" aria-label="Collage of sample printed pieces: classic car mailer, spa flyer, letterhead, envelopes and brochures"></div>
  <div class="model-photo" role="img" aria-label="Smiling woman on a medical brochure sample"></div>

  <div class="offer-banner">SPECIAL OFFER !</div>
  <ul class="offer-list">
    <li>Double your order FREE (order 500 business cards and get 1000)</li>
    <li>250 100lb gloss stock brochures 99.00</li>
    <li>Business packages (cards, envelopes and letterhead) 299</li>
    <li>1000 flyers 140.40</li>
    <li>5000 postcards 179.99</li>
  </ul>

  <p class="route-drop">Reach new customers at home without their address through <strong>Open Porch Route Drop</strong>.</p>

  <div class="order-info">
    <p>24 hr/7 Day</p>
    <p>orders@inkwillow.com</p>
    <p class="logo-placeholder">YOUR LOGO HERE</p>
  </div>
</section>

<section class="postcard postcard--back" aria-label="Postcard back">
  <div class="service-field">
    <span class="service-row">&nbsp;banners • <span class="service--lime">booklets</span> • booklets • brochures • <span class="service--cyan">brochures</span> • brochures</span>
    <span class="service-row">booklets • brochures • business cards • <span class="service--lime">catalogs</span> • calendars</span>
    <span class="service-row">&nbsp;&nbsp;brochures • <span class="service--cyan">business cards</span> • <span class="service--cyan">calendars</span> • CD/DVD packages</span>
    <span class="service-row">business cards • <span class="service--lime">calendars</span> • catalogs • catalogs • <span class="service--cyan">envelopes</span> • envelopes</span>
    <span class="service-row">calendars • <span class="service--cyan">catalogs</span> • <span class="service--lime">CD/DVD packages</span> • <span class="service--cyan">event tickets</span> • <span class="service--cyan">flyers</span></span>
    <span class="service-row">catalogs • CD/DVD packages • <span class="service--cyan">envelopes</span> • flyers • <span class="service--lime">flyers</span> • hangtags</span>
    <span class="service-row">CD/DVD packages • envelopes • <span class="service--lime">event tickets</span> • <span class="service--lime">hangtags</span> • <span class="service--cyan">hangtags</span></span>
    <span class="service-row">envelopes • event tickets • <span class="service--cyan">flyers</span> • hangtags • postcards • <span class="service--lime">postcards</span></span>
    <span class="service-row">event tickets • flyers • <span class="service--lime">hangtags</span> • <span class="service--cyan">postcards</span> • <span class="service--cyan">posters</span> • posters</span>
    <span class="service-row">flyers • hangtags • postcards • <span class="service--lime">posters</span> • posters • presentation folders</span>
    <span class="service-row">hangtags • postcards • posters • <span class="service--cyan">presentation folders</span> • rack cards • <span class="service--cyan">labels</span></span>
    <span class="service-row">postcards • posters • <span class="service--lime">rack cards</span> • <span class="service--lime">labels</span> • labels • <span class="service--lime">table tents</span></span>
    <span class="service-row">presentation folders • rack cards • <span class="service--cyan">labels</span> • table tents • <span class="service--cyan">window cling and decal</span></span>
    <span class="service-row">rack cards • <span class="service--cyan">labels</span> • <span class="service--lime">table tents</span> • window cling and decal • banners • <span class="service--lime">banners</span></span>
    <span class="service-row">labels • table tents • window cling and decal • banners • booklets</span>
  </div>
  <div class="stamp-zone">
    <div class="stamp-box">Postage<br>Stamp</div>
  </div>
</section>

</body>
</html>
```